New Business card design to reflect rebrand

I would like a business card design with a good base colour for our new logo and also a placeholder for a profile pic of the card holder. the design needs to be editable to the point that we can easily change the picture of the person and use that design for printmerlo etc. we are looking at a metalic finish business card so will need a good base colour to bring out the finish.

Target Market(s)

prospective customers

Industry/Entity Type

Business

Contact Information for Business Card

I would like one editable design that we can change the name of the card holder and profile picture. The design need to be in a format that be send to printmerlo etc.

Our address is Fenwick Lodge, Copse Lane, Ashbury Green, GU14 3TP Tel no. 01483 556172

Requirements
Must have
• place holder for a profile pic for the card holder. in AI or preferably PSD format

```html
<!DOCTYPE html>
<html lang="en">
<head>
<meta charset="utf-8">
<title>Brackenfold Workplace Services – Business Card</title>
<link rel="stylesheet" href="https://fonts.googleapis.com/css2?family=Open+Sans:wght@400;600;700&display=swap">
<style>
  :root {
    --canvas-bg: #2b2b2d;
    --card-bg: #151516;
    --card-bg-edge: #1d1d1f;
    --accent-orange: #e8731c;
    --brand-slate: #56708f;
    --text-light: #ecebea;
    --photo-top: #6b6b74;
    --photo-bottom: #2a2738;
  }
  * { box-sizing: border-box; margin: 0; padding: 0; }
  html, body {
    width: 1200px; height: 900px; overflow: hidden;
    background: var(--canvas-bg);
    font-family: "Open Sans", Arial, sans-serif;
  }
  .sheet {
    position: relative; width: 1200px; height: 900px;
    display: flex; align-items: center; justify-content: center; gap: 60px;
  }
  .card {
    position: relative; width: 525px; height: 300px;
    border-radius: 18px; overflow: hidden;
    background: linear-gradient(135deg, var(--card-bg-edge), var(--card-bg));
    box-shadow: 0 14px 30px rgba(0,0,0,.45);
  }
  .card-front .profile-photo {
    position: absolute; left: 0; bottom: 0;
    width: 250px; height: 255px;
    background: radial-gradient(ellipse at 50% 30%, var(--photo-top), var(--photo-bottom) 75%);
    border-top-right-radius: 120px 60px;
  }
  .card-front .details {
    position: absolute; left: 290px; top: 48px; right: 20px;
    color: var(--text-light); font-size: 13px; line-height: 1.55;
  }
  .holder-name {
    color: var(--accent-orange); font-weight: 700; font-size: 17px;
    margin-bottom: 14px;
  }
  .contact-line { display: flex; align-items: center; gap: 8px; }
  .contact-line svg { width: 11px; height: 11px; fill: var(--accent-orange); flex: none; }
  .address { margin-top: 22px; }
  .card-back {
    display: flex; flex-direction: column; align-items: center; justify-content: center;
  }
  .brand-name {
    color: var(--brand-slate); font-weight: 700; text-align: center;
    font-size: 36px; letter-spacing: 1px; line-height: 1.1;
  }
  .brand-name .brand-sub { display: block; font-size: 17px; letter-spacing: 4px; }
</style>
</head>
<body>
<main class="sheet">
  <section class="card card-front" aria-label="Business card front">
    <div class="profile-photo" role="img" aria-label="Profile photo of the card holder in a dark suit"></div>
    <div class="details">
      <p class="holder-name">Daniel Harrow</p>
      <p class="contact-line">
        <svg viewBox="0 0 24 24" aria-hidden="true"><path d="M6.6 10.8a15.1 15.1 0 0 0 6.6 6.6l2.2-2.2a1 1 0 0 1 1-.25 11.4 11.4 0 0 0 3.6.57 1 1 0 0 1 1 1V20a1 1 0 0 1-1 1A17 17 0 0 1 3 4a1 1 0 0 1 1-1h3.5a1 1 0 0 1 1 1c0 1.25.2 2.45.57 3.57a1 1 0 0 1-.25 1z"/></svg>
        01483 556172
      </p>
      <p class="contact-line">
        <svg viewBox="0 0 24 24" aria-hidden="true"><path d="M2 6h20v1.2l-10 7-10-7zM2 9.6l10 7 10-7V19H2z"/></svg>
        info@brackenfold.com
      </p>
      <p class="address">Fenwick Lodge, Copse Lane,<br>Ashbury Green, GU14 3TP</p>
    </div>
  </section>
  <section class="card card-back" aria-label="Business card back">
    <p class="brand-name">BRACKENFOLD<span class="brand-sub">WORKPLACE SERVICES</span></p>
  </section>
</main>
</body>
</html>
```